Update our OBGYN business card look and info

We are an OBGYN office. Our logo is nice but would like to "woman" part of the logo to be a darker color, to contrast with the flower that surrounds it. Maybe make our practice name Bloom Harbor Health more feminine. Our practice caters to women only. All providers and staff are female.

Target Market(s)

Females 16-65.

Industry/Entity Type

Business

Contact Information for Business Card

See attached upload. The ONLY CHANGE to the information is DELETE the name Paula Renwick, Midwife and REPLACE with Dora Fintelli, Midwife

Logo Text

Bloom Harbor Health Obstetrics & Gynecology

Font styles to use
Serif
Script

Colors
85cae6
0692cd
33a6d7
85abd2
f59195
eea4c8
cadf82
fac994
d3a5cc

```html
<!DOCTYPE html>
<html lang="en">
<head>
<meta charset="utf-8">
<title>Bloom Harbor Health – Business Card</title>
<link rel="stylesheet" href="https://fonts.googleapis.com/css2?family=Tinos:wght@400;700&display=swap">
<style>
  :root {
    --stage: #2b2b2d;
    --card-white: #ffffff;
    --brand-blue: #0692cd;
    --brand-mid: #33a6d7;
    --brand-light: #85cae6;
    --band-pale: #b9def0;
    --text-on-blue: #ffffff;
  }
  * { margin: 0; padding: 0; box-sizing: border-box; }
  html, body { width: 1200px; height: 880px; overflow: hidden; }
  body {
    background: var(--stage);
    font-family: "Tinos", "Times New Roman", serif;
    position: relative;
  }
  .card {
    position: absolute;
    width: 620px;
    height: 354px;
    border-radius: 22px;
    overflow: hidden;
    box-shadow: 0 10px 24px rgba(0,0,0,0.45);
  }
  /* Front */
  .card-front { left: 150px; top: 50px; background: var(--card-white); }
  .front-mark {
    position: absolute; left: 0; right: 0; top: 118px;
    display: flex; align-items: center; justify-content: center; gap: 14px;
  }
  .mark-dot {
    width: 34px; height: 34px; border-radius: 50%;
    background: var(--brand-mid);
  }
  .front-name {
    color: var(--brand-blue);
    font-size: 34px;
    font-weight: 400;
  }
  .front-url {
    position: absolute; left: 0; right: 0; top: 214px;
    text-align: center;
    color: var(--brand-mid);
    font-size: 17px;
    letter-spacing: 2px;
  }
  /* Back */
  .card-back { left: 430px; top: 476px; background: var(--brand-blue); }
  .back-wave { position: absolute; inset: 0; }
  .back-logo {
    position: absolute; right: 40px; top: 26px;
    display: flex; align-items: center; gap: 12px;
    color: var(--brand-blue);
    font-weight: 400;
  }
  .back-logo .mark-dot { width: 40px; height: 40px; }
  .logo-text { line-height: 1.05; }
  .logo-name { font-size: 32px; display: block; }
  .logo-specialty { font-size: 13px; letter-spacing: 1.2px; text-transform: uppercase; display: block; margin-top: 4px; }
  .provider-list {
    position: absolute; left: 40px; top: 170px;
    list-style: none;
    color: var(--text-on-blue);
    font-size: 17px;
    line-height: 21px;
  }
  .contact-list {
    position: absolute; left: 40px; top: 284px;
    list-style: none;
    color: var(--text-on-blue);
    font-size: 16px;
    line-height: 21px;
  }
  .contact-list li { display: flex; align-items: center; gap: 8px; }
  .contact-icon { width: 16px; height: 16px; flex: none; }
  .office-address {
    position: absolute; right: 36px; top: 176px;
    text-align: right;
    color: var(--text-on-blue);
    font-size: 17px;
    line-height: 21px;
    font-style: normal;
  }
</style>
</head>
<body>

<section class="card card-front" aria-label="Card front">
  <div class="front-mark">
    <span class="mark-dot"></span>
    <span class="front-name">Bloom Harbor Health</span>
  </div>
  <p class="front-url">www.bloomharborhealth.com</p>
</section>

<section class="card card-back" aria-label="Card back">
  <svg class="back-wave" viewBox="0 0 620 354" width="620" height="354" aria-hidden="true">
    <path d="M150 0 C205 110 335 162 455 152 C540 145 590 124 620 112 L620 0 Z" fill="var(--band-pale)"/>
    <path d="M172 0 C225 96 345 142 460 134 C545 128 592 108 620 98 L620 0 Z" fill="var(--card-white)"/>
  </svg>

  <div class="back-logo">
    <span class="mark-dot"></span>
    <span class="logo-text">
      <span class="logo-name">Bloom Harbor Health</span>
      <span class="logo-specialty">Obstetrics &amp; Gynecology</span>
    </span>
  </div>

  <ul class="provider-list">
    <li>Marian Okafor, MD</li>
    <li>Helen Castellane, MD</li>
    <li>Ruth Delacroix, MD</li>
    <li>Dora Fintelli, Midwife</li>
    <li>Lena Marchetti, Midwife</li>
  </ul>

  <ul class="contact-list">
    <li>
      <svg class="contact-icon" viewBox="0 0 16 16" aria-hidden="true"><circle cx="8" cy="8" r="7.2" fill="none" stroke="#fff" stroke-width="1.2"/><rect x="5.5" y="3.8" width="5" height="8.4" rx="1" fill="none" stroke="#fff" stroke-width="1.1"/></svg>
      555-014-2270
    </li>
    <li>
      <svg class="contact-icon" viewBox="0 0 16 16" aria-hidden="true"><circle cx="8" cy="8" r="7.2" fill="none" stroke="#fff" stroke-width="1.2"/><rect x="4.2" y="6.5" width="7.6" height="4" rx="0.8" fill="#fff"/><rect x="5.5" y="4" width="5" height="2.5" fill="none" stroke="#fff" stroke-width="1"/></svg>
      555-014-2291
    </li>
    <li>
      <svg class="contact-icon" viewBox="0 0 16 16" aria-hidden="true"><circle cx="8" cy="8" r="7.2" fill="none" stroke="#fff" stroke-width="1.2"/><circle cx="8" cy="8" r="4.3" fill="none" stroke="#fff" stroke-width="1"/><path d="M3.7 8 H12.3 M8 3.7 V12.3" stroke="#fff" stroke-width="0.9"/></svg>
      www.bloomharborhealth.com
    </li>
  </ul>

  <address class="office-address">
    418 Linden Row, Ste 3B<br>
    Larkfield, GA 30911-4402
  </address>
</section>

</body>
</html>
```